Flyer für Photovoltaik- und Energiesysteme
Zielgruppe
Die Merkling Strom GmbH entwickelt und realisiert seit über 20 Jahren Photovoltaik- und Energiesysteme für Unternehmen, Kommunen und öffentliche Einrichtungen.
Ziel dieses Flyers sind Bürgermeister, Oberbürgermeister, Kämmerer, Bauämter und kommunale Entscheidungsträger sowie Gemeinderatsmitglieder und Mitarbeiter der Gemeinden und Städte.
Der Flyer soll zeigen, dass Kommunen auch bei knappen Haushalten wirtschaftlich von Photovoltaik profitieren können. Dabei sollen insbesondere Bürgersolaranlagen, Fremdfinanzierung, Eigenverbrauchskonzepte und Energy Sharing verständlich und positiv dargestellt werden.
Der Flyer soll Vertrauen schaffen, Kompetenz vermitteln und zu einem persönlichen Gespräch motivieren.
Aufgabenstellung
Modernes, hochwertiges und professionelles Design. Wahrscheinlich DIN A4 Hochformat, offen für Vorschläge.
Zielgruppe sind Kommunen und öffentliche Entscheidungsträger, daher bitte keine „Werbeflyer Optik“, sondern seriös, vertrauenswürdig und wirtschaftlich.
Farben und Corporate Design an Merkling Strom anlehnen (Grün- und Weißtöne).
Merkling Strom Logo verwenden.
Bildsprache:
• moderne Rathäuser und Kommunalgebäude
• Photovoltaikanlagen auf öffentlichen Gebäuden
• Bürgerbeteiligung und regionale Wertschöpfung
• nachhaltige und wirtschaftliche Energieversorgung
Die Kernaussage lautet:
„Kommunen – Chancen nutzen, auch in Zeiten knapper Budgets.“
Folgende Lösungswege könnten grafisch dargestellt werden:
A) Eigenerzeugung Kommunale PV Anlagen auf eigenen Gebäuden (Eigeninvestion)
B) Ohne eigene Investition durch
-Stromverkaufsmodelle (onside PPA)
-Bürgersolaranlagen und Fremdfinanzierung
C) Energy Sharing (seit Juni 2026 möglich)
Lokale Nutzung und Verteilung erneuerbarer Energie.
Der Flyer soll vermitteln, dass die Energiewende nicht an fehlenden Haushaltsmitteln scheitern muss. Ich habe erste Entwurfe bereits von ChatGPT machen lassen, Text, Layout und Inhalt gefallen mir aber selbst eigentlich nicht und dienen eher ein wenig zur Inspiration und Verständnis.
Wichtig: Wenig Text, starke Grafiken, moderne Icons und eine hochwertige Gestaltung. Der Flyer soll eher wie eine Management Broschüre als wie ein klassischer Werbeflyer wirken.

```html
<!DOCTYPE html>
<html lang="de">
<head>
<meta charset="utf-8">
<title>Merkling Strom – Photovoltaik für Kommunen</title>
<link href="https://fonts.googleapis.com/css2?family=Barlow+Semi+Condensed:wght@500;600&family=Inter:wght@400;600;700&display=swap" rel="stylesheet">
<style>
  :root {
    --backdrop: #646464;
    --green: #00614f;
    --green-line: #2f7d6c;
    --ink: #1f2326;
    --muted: #4a4f53;
    --white: #ffffff;
    --footer: #2a2a2a;
  }
  * { margin: 0; padding: 0; box-sizing: border-box; }
  html, body { width: 980px; height: 1200px; overflow: hidden; background: var(--backdrop); }
  body { position: relative; font-family: "Inter", sans-serif; color: var(--ink); }

  .flyer { position: absolute; left: 195px; top: 183px; width: 589px; height: 833px; background: var(--white); overflow: hidden; }

  .hero { position: absolute; left: 0; top: 0; width: 589px; height: 413px; }
  .hero-photo { position: absolute; inset: 0;
    background: linear-gradient(180deg, #164760 0%, #3f7891 22%, #6f98ab 38%, #55636c 52%, #3b434b 72%, #2a2f35 100%); }
  .hero-shade { position: absolute; inset: 0; background: linear-gradient(90deg, rgba(20,24,28,.45) 0%, rgba(20,24,28,0) 70%); }

  .brand { position: absolute; left: 41px; top: 48px; display: flex; align-items: center; gap: 9px; }
  .brand-mark { width: 26px; height: 26px; border: 2px solid var(--white); }
  .brand-name { font-family: "Barlow Semi Condensed", sans-serif; font-weight: 600; font-size: 21px; color: var(--white); letter-spacing: .3px; }

  .headline { position: absolute; left: 36px; top: 263px; font-family: "Barlow Semi Condensed", sans-serif; font-weight: 500;
    font-size: 29px; line-height: 28.5px; color: var(--white); text-transform: uppercase; letter-spacing: .2px; }
  .subline { position: absolute; left: 36px; top: 362px; width: 340px; font-size: 13.5px; line-height: 17px; color: #eef1f2; }

  .overview { position: absolute; left: 0; top: 413px; width: 589px; height: 282px; }
  .overview-title { position: absolute; left: 36px; top: 23px; font-family: "Barlow Semi Condensed", sans-serif; font-weight: 600; font-size: 17.5px; color: var(--ink); }
  .rule { position: absolute; left: 36px; width: 517px; }
  .rule-strong { top: 49px; height: 2px; background: var(--green); }
  .rule-thin { height: 1px; background: var(--green-line); }

  .option { position: absolute; left: 36px; width: 517px; }
  .option-title { position: absolute; left: 0; top: 0; font-family: "Barlow Semi Condensed", sans-serif; font-weight: 500; font-size: 13.5px; color: var(--ink); }
  .option-text { position: absolute; left: 0; width: 180px; font-size: 9px; line-height: 13px; color: var(--muted); }
  .benefits { position: absolute; list-style: none; }
  .benefits li { font-size: 9px; line-height: 15.8px; color: var(--muted); padding-left: 11px; position: relative; }
  .benefits li::before { content: ""; position: absolute; left: 1px; top: 5px; border-left: 5px solid var(--ink); border-top: 3px solid transparent; border-bottom: 3px solid transparent; }
  .model-title { position: absolute; font-size: 9.5px; font-weight: 600; color: var(--ink); }

  .contact-band { position: absolute; left: 0; top: 695px; width: 589px; height: 112px; background: var(--green); color: var(--white); }
  .band-col { position: absolute; top: 20px; }
  .band-title { font-size: 11.5px; font-weight: 700; line-height: 14px; }
  .band-text { margin-top: 6px; font-size: 9.8px; line-height: 14px; color: #dbe9e5; }
  .band-cta { display: inline-flex; align-items: center; gap: 3px; margin-top: 14px; font-size: 9.5px; font-weight: 700; color: var(--white); text-decoration: none; }

  .footer { position: absolute; left: 0; top: 807px; width: 589px; height: 26px; background: var(--footer); color: var(--white); }
  .footer-claim { position: absolute; left: 40px; top: 7px; font-size: 9.8px; }
  .footer-web { position: absolute; right: 34px; top: 6px; font-size: 9.8px; font-weight: 600; letter-spacing: .8px; }
</style>
</head>
<body>
<main class="flyer">
  <section class="hero">
    <div class="hero-photo" role="img" aria-label="Fotografie: zwei Monteure mit Schutzhelmen installieren Solarmodule auf einem Dach unter blauem Himmel"></div>
    <div class="hero-shade"></div>
    <div class="brand"><span class="brand-mark"></span><span class="brand-name">Merkling Strom</span></div>
    <h1 class="headline">Kommunen Chancen<br>nutzen, auch in Zeiten<br>knapper Budgets.</h1>
    <p class="subline">Photovoltaik für Kommunen – auch ohne eigene Investition möglich.</p>
  </section>

  <section class="overview">
    <h2 class="overview-title">Ihre Möglichkeiten im Überblick</h2>
    <div class="rule rule-strong"></div>

    <div class="option" style="top:70px;">
      <h3 class="option-title">Eigeninvestition</h3>
      <p class="option-text" style="top:22px;">Die Kommune investiert selbst.</p>
      <ul class="benefits" style="left:212px; top:-3px;">
        <li>Höchste Wirtschaftlichkeit</li>
        <li>Volle Kontrolle</li>
        <li>Amortisation häufig unter 10 Jahren</li>
      </ul>
    </div>
    <div class="rule rule-thin" style="top:126px;"></div>

    <div class="option" style="top:135px;">
      <h3 class="option-title">Ohne Investition</h3>
      <p class="option-text" style="top:22px;">PV-Anlage ohne finanzielle Vorleistung der Kommune.</p>
      <span class="model-title" style="left:212px; top:-1px;">Onsite PPA/Fremdbetrieb</span>
      <ul class="benefits" style="left:212px; top:12px;">
        <li>Keine Investition</li>
        <li>Planbare Stromkosten</li>
        <li>Betrieb durch Dritte</li>
      </ul>
      <span class="model-title" style="left:375px; top:-1px;">Bürgersolar</span>
      <ul class="benefits" style="left:375px; top:11px;">
        <li style="line-height:14px;">Finanzierung durch Bürger</li>
        <li style="line-height:14px;">Regionale Wertschöpfung</li>
        <li style="line-height:14px;">Hohe Akzeptanz</li>
      </ul>
    </div>
    <div class="rule rule-thin" style="top:204px;"></div>

    <div class="option" style="top:214px;">
      <h3 class="option-title">Energy Sharing</h3>
      <p class="option-text" style="top:22px;">PV-Strom lokal gemeinsam nutzen und verteilen.</p>
      <ul class="benefits" style="left:212px; top:-3px;">
        <li>Höherer Eigenverbrauch</li>
        <li>Kosten senken</li>
        <li>Versorgungssicherheit stärken</li>
      </ul>
    </div>
  </section>

  <section class="contact-band">
    <div class="band-col" style="left:36px; width:245px;">
      <h3 class="band-title">Warum Merkling Strom?</h3>
      <p class="band-text">Über 20 Jahre Erfahrung in der Entwicklung und Umsetzung von Photovoltaik- und Energiesystemen für Kommunen und öffentliche Einrichtungen.</p>
    </div>
    <div class="band-col" style="left:302px; width:250px;">
      <h3 class="band-title">Lassen Sie Uns Gemeinsam Ihre Lösung Finden.</h3>
      <p class="band-text">Wir beraten Sie individuell und unverbindlich.</p>
      <a class="band-cta" href="#">Jetzt Beraten Lassen
        <svg width="9" height="8" viewBox="0 0 9 8" aria-hidden="true"><path d="M0 4h7.5M4.5 1l3 3-3 3" fill="none" stroke="#fff" stroke-width="1.3"/></svg>
      </a>
    </div>
  </section>

  <footer class="footer">
    <span class="footer-claim">Nachhaltig. Regional. Zukunftssicher.</span>
    <span class="footer-web">merkling-strom-beispiel.de</span>
  </footer>
</main>
</body>
</html>
```